Vorn upkeep KT Solar Venture

Solar power system install
Services and maintenance
wiring, Rewinding and Renovation
Switch Board Upgrade
Power and lighting point
t doesn’t matter how much you spend on quality parts, your solar system will let you down if your design and installation are sub-par. Have your solar system tailored and installed by our Master Electrician and Bright Grid Guild Accredited team.

Target Market(s)

sales and installed

Industry/Entity Type

Solar install and retailer

Contact Information for Business Card

Name , Email, Phone Number ,Business address,

Font styles to use
Serif

Colors
0054AA
0677BA
7BADD7
CADEEF
E8F1F8

Requirements
Must have
• clear and bright
Nice to have
• new design
Should not have
• unclear pictures

```html
<!DOCTYPE html>
<html lang="en">
<head>
<meta charset="utf-8">
<title>Vorn upkeep – Business Card</title>
<link href="https://fonts.googleapis.com/css2?family=Roboto:wght@400;500&display=swap" rel="stylesheet">
<style>
  :root {
    --page: #dfe4e9;
    --deep-blue: #0054AA;
    --mid-blue: #0677BA;
    --sky-blue: #7BADD7;
    --pale-blue: #CADEEF;
    --mist: #E8F1F8;
    --leaf: #3f9a2e;
    --lime: #8cc63f;
    --text-light: #e6eef6;
  }
  html, body {
    margin: 0;
    width: 1200px;
    height: 1054px;
    overflow: hidden;
    background: var(--page);
  }
  .card {
    position: absolute;
    left: 100px;
    top: 227px;
    width: 1000px;
    height: 600px;
    filter: drop-shadow(0 10px 24px rgba(0,0,0,0.18));
  }
  .card text { font-family: "Roboto", sans-serif; }
  .brand-name { font-weight: 500; font-size: 46px; fill: var(--deep-blue); }
  .person-name { font-weight: 500; font-size: 36px; fill: var(--lime); }
  .person-role { font-weight: 400; font-size: 24px; fill: var(--text-light); }
  .contact { font-weight: 400; font-size: 24px; fill: var(--text-light); }
  .tagline { font-weight: 400; font-size: 24px; fill: var(--mist); }
  .icon { fill: var(--lime); }
</style>
</head>
<body>
<svg class="card" viewBox="0 0 1000 600" xmlns="http://www.w3.org/2000/svg">
  <defs>
    <clipPath id="card-shape"><rect width="1000" height="600" rx="18"/></clipPath>
    <clipPath id="blue-side">
      <path d="M402,0 C470,110 520,250 490,380 C470,470 430,560 390,600 L1000,600 L1000,0 Z"/>
    </clipPath>
    <linearGradient id="left-face" x1="0" y1="0" x2="1" y2="1">
      <stop offset="0" stop-color="#ffffff"/>
      <stop offset="1" stop-color="var(--mist)"/>
    </linearGradient>
    <linearGradient id="blue-face" x1="0" y1="0" x2="1" y2="1">
      <stop offset="0" stop-color="var(--mid-blue)"/>
      <stop offset="1" stop-color="var(--deep-blue)"/>
    </linearGradient>
    <linearGradient id="green-band" x1="0" y1="0" x2="1" y2="0">
      <stop offset="0" stop-color="var(--leaf)"/>
      <stop offset="1" stop-color="var(--lime)"/>
    </linearGradient>
  </defs>

  <g clip-path="url(#card-shape)">
    <rect class="card-face" width="1000" height="600" fill="url(#left-face)"/>
    <path class="curve-accent" d="M390,0 C458,110 508,250 478,380 C458,470 418,560 378,600"
          fill="none" stroke="var(--leaf)" stroke-width="26"/>
    <g clip-path="url(#blue-side)">
      <rect class="info-panel" width="1000" height="600" fill="url(#blue-face)"/>
      <rect class="tagline-band" x="0" y="514" width="1000" height="60" fill="url(#green-band)"/>
    </g>
  </g>

  <!-- brand block -->
  <circle class="brand-dot" cx="88" cy="300" r="22" fill="var(--sky-blue)"/>
  <text class="brand-name" x="124" y="316">Vorn upkeep</text>

  <!-- person -->
  <text class="person-name" x="559" y="118">Mara Ellison</text>
  <text class="person-role" x="559" y="160">Managing Director</text>

  <!-- address -->
  <text class="contact" x="559" y="292">87 Linden Row, Harbor Vale,</text>
  <text class="contact" x="559" y="329">Eastbrook, US 482190</text>

  <!-- phone -->
  <path class="icon" d="M561,370 h18 a3,3 0 0 1 3,3 v3 h-6 v-2 h-12 v2 h-6 v-3 a3,3 0 0 1 3,-3 Z M562,378 h16 l3,8 h-22 Z"/>
  <text class="contact" x="609" y="386">555-204-7788</text>

  <!-- email -->
  <rect class="icon" x="558" y="405" width="22" height="15" rx="1"/>
  <path d="M558,406 L569,414 L580,406" fill="none" stroke="#0a5fa8" stroke-width="2"/>
  <text class="contact" x="609" y="422">mara@vornupkeep.com</text>

  <!-- web -->
  <circle cx="569" cy="450" r="9" fill="none" stroke="var(--lime)" stroke-width="2"/>
  <ellipse cx="569" cy="450" rx="4" ry="9" fill="none" stroke="var(--lime)" stroke-width="1.5"/>
  <line x1="560" y1="450" x2="578" y2="450" stroke="var(--lime)" stroke-width="1.5"/>
  <text class="contact" x="609" y="458">www.vornupkeep.com</text>

  <!-- tagline -->
  <text class="tagline" x="559" y="552">Solar power system install</text>
</svg>
</body>
</html>
```